KRT Project Signage

Need a sign to be displayed in the front of properties currently under Construction or Renovation to advertise our company information. Need it to be Professional and Contemporary. We are a Design/Build Construction Company. Information should include Company Name, email, website, phone number. Attached: Logo and company brochure, also included and inspiration images

```html
<!DOCTYPE html>
<html lang="en">
<head>
<meta charset="utf-8">
<title>KRT Project Signage – Options</title>
<link rel="stylesheet" href="https://fonts.googleapis.com/css2?family=Playfair+Display:wght@400;500&family=Montserrat:wght@300;400&display=swap">
<style>
  :root {
    --paper: #fdfdf8;
    --sign: #ffffff;
    --ink: #0b0b0b;
    --yellow: #ecea4a;
    --label: #111111;
    --serif: "Playfair Display", serif;
    --sans: "Montserrat", sans-serif;
  }
  * { box-sizing: border-box; margin: 0; padding: 0; }
  html, body { width: 1200px; height: 1200px; overflow: hidden; }
  body { background: var(--paper); position: relative; font-family: var(--sans); }

  .option { position: absolute; top: 330px; width: 540px; height: 540px; }
  .option--serif { left: 40px; }
  .option--sans { left: 620px; }
  .option__number {
    position: absolute; top: -70px; left: -6px;
    font-family: var(--sans); font-weight: 300; font-size: 34px; color: var(--label);
  }

  .sign {
    position: absolute; inset: 0;
    background: var(--sign);
    box-shadow: 8px 8px 10px rgba(0,0,0,0.28);
    overflow: visible;
  }
  .option--serif .sign { --face: var(--serif); }
  .option--sans .sign { --face: var(--sans); }

  .sign__brand {
    position: absolute; top: 0; left: 0; right: 0; height: 164px;
    display: flex; align-items: center; justify-content: center; gap: 10px;
  }
  .sign__brand-dot { width: 22px; height: 22px; border-radius: 50%; background: var(--yellow); }
  .sign__brand-name {
    font-family: var(--face); font-weight: 400; font-size: 24px;
    letter-spacing: 1px; color: var(--ink);
  }

  .sign__band {
    position: absolute; top: 164px; left: 0; right: 0; height: 101px;
    background: var(--ink); color: var(--yellow);
    display: flex; flex-direction: column; align-items: center; justify-content: center;
  }
  .sign__title {
    font-family: var(--face); line-height: 1; white-space: nowrap;
  }
  .option--serif .sign__title { font-size: 48px; font-weight: 500; transform: scaleX(0.9); }
  .option--sans .sign__title { font-size: 45px; font-weight: 300; }
  .sign__tagline {
    margin-top: 12px; font-family: var(--face); font-size: 14px;
    letter-spacing: 9px; color: #f2f2f2; white-space: nowrap;
  }
  .option--sans .sign__tagline { font-weight: 300; }

  .contact { position: absolute; left: 124px; height: 51px; width: 292px; }
  .contact--email { top: 310px; }
  .contact--web { top: 379px; }
  .contact__icon {
    position: absolute; left: 0; top: 0; width: 53px; height: 51px;
    background: var(--ink); display: flex; align-items: center; justify-content: center;
  }
  .contact__icon::before {
    content: ""; position: absolute; left: -2px; top: 0; bottom: 0; width: 2px; background: var(--yellow);
  }
  .contact__text {
    position: absolute; left: 53px; top: 4px; width: 239px; height: 40px;
    background: var(--yellow); color: var(--ink);
    display: flex; align-items: center; justify-content: center;
    font-family: var(--face); font-size: 15px; white-space: nowrap;
  }
  .option--sans .contact__text { font-weight: 300; }

  .phone { position: absolute; left: 81px; top: 459px; width: 403px; height: 69px; }
  .phone__bar {
    position: absolute; left: 0; top: 6px; width: 403px; height: 57px; background: var(--ink);
    display: flex; align-items: center; padding-left: 82px;
    color: var(--yellow); font-family: var(--face); font-size: 38px; white-space: nowrap;
  }
  .option--serif .phone__bar { justify-content: center; padding-left: 70px; }
  .option--sans .phone__bar { letter-spacing: 3px; font-weight: 400; }
  .phone__icon {
    position: absolute; left: 5px; top: 0; width: 62px; height: 69px; background: var(--yellow);
    display: flex; align-items: center; justify-content: center;
  }
</style>
</head>
<body>

<section class="option option--serif" aria-label="Sign option 1">
  <span class="option__number">1</span>
  <div class="sign">
    <div class="sign__brand"><span class="sign__brand-dot"></span><span class="sign__brand-name">KRT CONSTRUCTION</span></div>
    <div class="sign__band">
      <div class="sign__title">KRT CONSTRUCTION</div>
      <div class="sign__tagline">LUXRY RENOVATION↙</div>
    </div>
    <div class="contact contact--email">
      <div class="contact__icon"><svg width="28" height="22" viewBox="0 0 28 22"><rect x="2" y="2" width="24" height="18" rx="2" fill="none" stroke="#ecea4a" stroke-width="2.5"/><path d="M3 4l11 9 11-9" fill="none" stroke="#ecea4a" stroke-width="2.5"/></svg></div>
      <div class="contact__text">info@krtconstruction.com</div>
    </div>
    <div class="contact contact--web">
      <div class="contact__icon"><svg width="28" height="28" viewBox="0 0 28 28"><circle cx="14" cy="14" r="12" fill="#ecea4a"/><ellipse cx="14" cy="14" rx="5" ry="12" fill="none" stroke="#0b0b0b" stroke-width="1.6"/><path d="M2 14h24M4 8h20M4 20h20" stroke="#0b0b0b" stroke-width="1.6"/></svg></div>
      <div class="contact__text">www.krtconstruction.com</div>
    </div>
    <div class="phone">
      <div class="phone__bar">555-014-2276</div>
      <div class="phone__icon"><svg width="32" height="32" viewBox="0 0 24 24"><path d="M6.6 2.5l3 3.4-1.9 2.6c1.3 2.9 3.9 5.5 6.8 6.8l2.6-1.9 3.4 3-1.6 3.2c-.5.7-1.4 1-2.2.8C9.6 18.8 5.2 14.4 3.6 7.3c-.2-.8.1-1.7.8-2.2z" fill="none" stroke="#0b0b0b" stroke-width="1.6" stroke-linejoin="round"/></svg></div>
    </div>
  </div>
</section>

<section class="option option--sans" aria-label="Sign option 2">
  <span class="option__number">2</span>
  <div class="sign">
    <div class="sign__brand"><span class="sign__brand-dot"></span><span class="sign__brand-name">KRT CONSTRUCTION</span></div>
    <div class="sign__band">
      <div class="sign__title">KRT CONSTRUCTION</div>
      <div class="sign__tagline">LUXRY RENOVATION↙</div>
    </div>
    <div class="contact contact--email">
      <div class="contact__icon"><svg width="28" height="22" viewBox="0 0 28 22"><rect x="2" y="2" width="24" height="18" rx="2" fill="none" stroke="#ecea4a" stroke-width="2.5"/><path d="M3 4l11 9 11-9" fill="none" stroke="#ecea4a" stroke-width="2.5"/></svg></div>
      <div class="contact__text">info@krtconstruction.com</div>
    </div>
    <div class="contact contact--web">
      <div class="contact__icon"><svg width="28" height="28" viewBox="0 0 28 28"><circle cx="14" cy="14" r="12" fill="#ecea4a"/><ellipse cx="14" cy="14" rx="5" ry="12" fill="none" stroke="#0b0b0b" stroke-width="1.6"/><path d="M2 14h24M4 8h20M4 20h20" stroke="#0b0b0b" stroke-width="1.6"/></svg></div>
      <div class="contact__text">www.krtconstruction.com</div>
    </div>
    <div class="phone">
      <div class="phone__bar">555-014-2276</div>
      <div class="phone__icon"><svg width="32" height="32" viewBox="0 0 24 24"><path d="M6.6 2.5l3 3.4-1.9 2.6c1.3 2.9 3.9 5.5 6.8 6.8l2.6-1.9 3.4 3-1.6 3.2c-.5.7-1.4 1-2.2.8C9.6 18.8 5.2 14.4 3.6 7.3c-.2-.8.1-1.7.8-2.2z" fill="none" stroke="#0b0b0b" stroke-width="1.6" stroke-linejoin="round"/></svg></div>
    </div>
  </div>
</section>

</body>
</html>
```